business card deign

Logo needs the following on it.
1. attached logo
2. Tagline - "From cold drinks to good times...we bring it all!"
3. Name- Dalton Pikes, Founder and CPO
4. Address - 412 E. Carver Avenue, Ste 2207, Tampa, FL. 33917
5. Phone - 555.318.4726

```html
<!DOCTYPE html>
<html lang="en">
<head>
<meta charset="utf-8">
<title>Bounder Business Card</title>
<link href="https://fonts.googleapis.com/css2?family=Roboto:wght@400;700&display=swap" rel="stylesheet">
<style>
  :root {
    --stage: #222222;
    --card-white: #ffffff;
    --card-black: #0d0d0d;
    --pattern-dark: #141414;
    --pattern-light: #6a6a6a;
    --ink: #111111;
    --rule: #1a1a1a;
    --shadow: rgba(0, 0, 0, 0.55);
  }
  * { box-sizing: border-box; margin: 0; padding: 0; }
  html, body {
    width: 1200px;
    height: 780px;
    overflow: hidden;
    background: var(--stage);
    font-family: "Roboto", Arial, sans-serif;
  }
  .card {
    position: absolute;
    width: 560px;
    height: 320px;
    border-radius: 26px;
    overflow: hidden;
    box-shadow: 0 14px 30px var(--shadow);
  }
  /* Back side */
  .card-back {
    left: 30px;
    top: 230px;
    background: var(--card-black);
  }
  .card-back .pattern {
    position: absolute;
    inset: 0;
    background: linear-gradient(200deg, var(--pattern-light) 0%, var(--pattern-dark) 45%, var(--card-black) 100%);
  }
  .card-back .brand-mark {
    position: absolute;
    right: 34px;
    bottom: 40px;
    display: flex;
    align-items: center;
    gap: 6px;
    color: var(--card-white);
    font-weight: 700;
    font-size: 11px;
    letter-spacing: 3px;
  }
  .brand-mark .dot {
    width: 8px;
    height: 8px;
    background: var(--card-white);
  }
  /* Front side */
  .card-front {
    left: 610px;
    top: 230px;
    background: var(--card-white);
    color: var(--ink);
  }
  .card-front .brand-name {
    position: absolute;
    left: 44px;
    top: 122px;
    font-weight: 700;
    font-size: 30px;
    line-height: 1;
    letter-spacing: 12px;
  }
  .card-front .tab {
    position: absolute;
    right: 0;
    top: 96px;
    width: 14px;
    height: 50px;
    background: var(--ink);
  }
  .card-front .person {
    position: absolute;
    right: 40px;
    top: 100px;
    text-align: right;
  }
  .person .name {
    font-weight: 700;
    font-size: 26px;
    line-height: 1.1;
  }
  .person .role {
    font-size: 15px;
    margin-top: 3px;
  }
  .card-front .rule {
    position: absolute;
    left: 44px;
    right: 40px;
    top: 172px;
    height: 1.5px;
    background: var(--rule);
  }
  .card-front .contact {
    position: absolute;
    left: 44px;
    bottom: 36px;
    list-style: none;
    font-size: 13px;
    line-height: 1.45;
  }
  .contact li {
    display: flex;
    align-items: flex-start;
    gap: 8px;
  }
  .contact svg {
    width: 13px;
    height: 13px;
    margin-top: 2px;
    flex: none;
  }
  .card-front .tagline {
    position: absolute;
    right: 40px;
    bottom: 56px;
    text-align: right;
    font-size: 13px;
    line-height: 1.45;
  }
</style>
</head>
<body>

<section class="card card-back" aria-label="Card back">
  <div class="pattern" role="img" aria-label="Repeating brand pattern in dark and silver tones"></div>
  <div class="brand-mark"><span class="dot"></span>BOUNDER</div>
</section>

<section class="card card-front" aria-label="Card front">
  <div class="brand-name">BOUNDER</div>

  <div class="tab"></div>
  <div class="person">
    <div class="name">Dalton Pikes</div>
    <div class="role">Founder and CPO</div>
  </div>

  <div class="rule"></div>

  <ul class="contact">
    <li>
      <svg viewBox="0 0 24 24" aria-hidden="true"><path fill="currentColor" d="M6.6 10.8a15 15 0 0 0 6.6 6.6l2.2-2.2a1 1 0 0 1 1-.25 11.4 11.4 0 0 0 3.6.57 1 1 0 0 1 1 1V20a1 1 0 0 1-1 1A17 17 0 0 1 3 4a1 1 0 0 1 1-1h3.5a1 1 0 0 1 1 1c0 1.25.2 2.450.57 3.6a1 1 0 0 1-.25 1z"/></svg>
      <span>555.318.4726</span>
    </li>
    <li>
      <svg viewBox="0 0 24 24" aria-hidden="true"><path fill="none" stroke="currentColor" stroke-width="2.2" d="M12 21s-6-6.2-6-11a6 6 0 0 1 12 0c0 4.8-6 11-6 11z"/><circle cx="12" cy="10" r="2.2" fill="currentColor"/></svg>
      <span>412 E. Carver Avenue,<br>Ste 2207, Tampa, FL. 33917</span>
    </li>
  </ul>

  <p class="tagline">From cold drinks to good times<br>...we bring it all!</p>
</section>

</body>
</html>
```